Tour operator needs simple coded WordPress site (updated extra payment for coding and guaranteed)

[update 9/7/2015]
If you design a new logo and it gets accepted, even if we use another template with your logo you will get $50
[update 8/7/2015]
Update on questions about dual-language
For dual languages we are happy to set up a second site with the same designs in a second language.
For the design aspect just allow the user to switch between languages with an icon.
For the coding, a replica of the site on a second server will do (to save messing around with multiple language plugins) - we will populate it with Chinese text
[original post]
Simple coded WordPress site for tours
You can choose to design only or design and code ($340 design, $150 bonus for coding)
Open design brief - use your creativity
Will be in 2 languages (English and Chinese) but design needs only to be in one language
Winning design will be chosen only from home page, but the winner must make a second standard template page when chosen at no extra cost.
Must be responsive design
We only need homepage and standard template page design and coding, we will populate the pages
You can use design ideas from our pamphlet if you like - attached
Only a sample logo and colors on website and pamphlet - feel free to change as the current ones seem restrictive
Current website framework only to give an idea of the number of pages and basic menu structure (no need to use existing navigation style or any style at all for that matter, open brief)
http://brightwattlejourneys.com.au/
Target Market(s)
Chinese parents of kids 10-14 (the kids will take the tour)
Industry/Entity Type
Tour
Number of Pages Required
2 page
Look and feel
Each slider illustrates characteristics of the customer's brand and the style your logo design should communicate.

```html
<!DOCTYPE html>
<html lang="en">
<head>
<meta charset="utf-8">
<title>Bright Wattle Journeys – Educational Tours</title>
<link href="https://fonts.googleapis.com/css2?family=Open+Sans:wght@400;600;700;800&display=swap" rel="stylesheet">
<style>
:root{
  --orange:#f5a623;
  --orange-dark:#e8921a;
  --cyan:#27b4d6;
  --green:#6f8f35;
  --green-overlay:rgba(104,140,48,.86);
  --ink:#4a4a4a;
  --muted:#8a8a8a;
  --line:#e6e6e6;
  --white:#ffffff;
  --navy:#1f3d6b;
}
*{box-sizing:border-box;margin:0;padding:0}
html,body{width:1200px;height:2384px;overflow:hidden;background:var(--white)}
body{font-family:"Open Sans",Arial,sans-serif;color:var(--ink);position:relative}
section,header,footer{position:absolute;left:0;width:1200px}

/* header */
.site-header{top:0;height:80px;background:var(--white);display:flex;align-items:center;justify-content:space-between;padding:0 56px}
.brand{display:flex;align-items:center;gap:10px;font-weight:700;font-size:24px;color:var(--navy)}
.brand-dot{width:14px;height:14px;border-radius:50%;background:var(--orange)}
.main-nav{display:flex;gap:6px}
.main-nav a{font-size:15px;font-weight:600;color:var(--ink);text-decoration:none;padding:8px 16px;border-radius:3px}
.main-nav a.active{background:var(--orange);color:var(--white)}

/* hero */
.hero{top:80px;height:420px;overflow:hidden}
.hero-photo{position:absolute;inset:0;background:linear-gradient(180deg,#6aa9d8 0%,#9cc6e6 45%,#c9a77a 78%,#3e5a72 100%)}
.hero-title{position:absolute;left:0;right:0;top:196px;text-align:center;color:var(--white);font-size:44px;font-weight:700;line-height:1.2;text-shadow:0 2px 8px rgba(0,0,0,.35)}
.hero-dots{position:absolute;left:0;right:0;top:380px;display:flex;justify-content:center;gap:10px}
.hero-dots span{width:12px;height:12px;border-radius:50%;background:rgba(255,255,255,.6)}
.hero-dots span.on{background:var(--white)}

/* about */
.about{top:500px;height:200px;background:var(--orange);text-align:center;color:var(--white)}
.section-title{font-size:30px;font-weight:700;letter-spacing:1px}
.about .section-title{margin-top:40px}
.about p{margin:22px auto 0;width:880px;font-size:17px;line-height:1.55}
.about-arrow{position:absolute;left:50%;bottom:-28px;margin-left:-30px}

/* intro */
.intro{top:700px;height:440px}
.intro-photo{position:absolute;left:150px;top:98px;width:300px;height:210px;border:6px solid var(--white);box-shadow:0 2px 10px rgba(0,0,0,.15);background:linear-gradient(135deg,#e9e2d6,#f0c99c 55%,#d68a5a)}
.intro-text{position:absolute;left:500px;top:100px;width:560px;font-size:13px;line-height:1.6;color:var(--muted)}
.intro-text p+p{margin-top:14px}
.btn{position:absolute;left:520px;top:344px;width:170px;height:40px;border-radius:20px;background:var(--green);color:var(--white);font-size:12px;font-weight:700;letter-spacing:.5px;display:flex;align-items:center;justify-content:center}

/* educational */
.educational{top:1140px;height:440px;background:var(--white)}
.edu-photo{position:absolute;left:0;top:0;width:560px;height:440px;background:linear-gradient(160deg,#d9d4cc 0%,#b9b3aa 40%,#e9a13c 75%,#f4b14a 100%)}
.edu-panel{position:absolute;left:410px;top:40px;width:790px;height:360px;background:var(--cyan);padding:40px 0 0 150px;color:var(--white)}
.edu-panel .section-title{font-size:30px}
.edu-list{list-style:none;margin-top:26px}
.edu-list li{display:flex;align-items:center;gap:14px;font-size:13px;line-height:1;margin-bottom:17px}
.edu-list li::before{content:"";width:8px;height:8px;border-radius:50%;background:var(--white)}

/* safe */
.safe{top:1580px;height:480px;text-align:center}
.safe .section-title{margin-top:56px;color:var(--orange)}
.title-rule{width:60px;height:3px;background:var(--orange);margin:14px auto 0}
.safe-cols{display:flex;gap:80px;padding:38px 140px 0;text-align:left}
.safe-cols ul{list-style:none;flex:1}
.safe-cols li{font-size:13px;line-height:1.5;color:var(--muted);padding:0 0 14px 16px;position:relative}
.safe-cols li::before{content:"";position:absolute;left:0;top:8px;width:6px;height:6px;border-radius:50%;background:var(--orange)}

/* includes */
.includes{top:2060px;height:240px;overflow:hidden}
.includes-photo{position:absolute;inset:0;background:linear-gradient(90deg,#5f7f2e,#7fa044 60%,#91ad5a)}
.includes-shade{position:absolute;inset:0;background:var(--green-overlay)}
.includes-title{position:absolute;left:52px;top:96px;font-size:34px;font-weight:700;color:var(--white);letter-spacing:1px}
.inc-cols{position:absolute;left:410px;top:34px;display:flex;gap:120px}
.inc-cols ul{list-style:none;width:300px}
.inc-cols li{display:flex;align-items:center;gap:14px;font-size:12px;color:var(--white);margin-bottom:12px}
.inc-cols svg{flex:none}

/* footer */
.site-footer{top:2300px;height:84px;background:var(--white);padding:20px 56px}
.foot-nav{display:flex;gap:16px;font-size:12px;color:var(--ink)}
.copyright{margin-top:8px;font-size:11px;color:var(--muted)}
.social{position:absolute;right:90px;top:22px;display:flex;gap:10px}
.social span{width:34px;height:34px;border-radius:50%}
.s1{background:#3ea9df}.s2{background:#3b5b98}.s3{background:#e0822d}
</style>
</head>
<body>

<header class="site-header">
  <div class="brand"><span class="brand-dot"></span>Bright Wattle</div>
  <nav class="main-nav">
    <a class="active">Home</a><a>Tours</a><a>Contact</a><a>About Us</a>
  </nav>
</header>

<section class="hero">
  <div class="hero-photo" role="img" aria-label="Sydney harbour skyline with the bridge and opera house at dusk"></div>
  <h1 class="hero-title">Educational, safe, culturally<br>enlightening and fun</h1>
  <div class="hero-dots"><span class="on"></span><span></span><span></span></div>
</section>

<section class="about">
  <h2 class="section-title">ABOUT</h2>
  <p>At Bright Wattle Journeys we are passionate about educational travel opportunities for students to gain academic and cultural understanding of Australia.</p>
  <svg class="about-arrow" width="60" height="30" viewBox="0 0 60 30"><polygon points="0,0 60,0 30,30" fill="#f5a623"/></svg>
</section>

<section class="intro">
  <div class="intro-photo" role="img" aria-label="Smiling student holding a phone outdoors"></div>
  <div class="intro-text">
    <p>As the premier cultural and educational tour host in Sydney, our program is educational, safe, culturally enlightening and fun. Students discover local schools, history, sport, food and culture, improving their English while gaining a real understanding of Australian life. Each visit is planned around meaningful experiences that build confidence and new friendships across cultures.</p>
    <p>Planning and guiding at Bright Wattle Journeys has a long history. Our team of dedicated experts works every day of the tour, from meeting you at arrival, planning each lesson and outing, to returning every student home safely and happy.</p>
  </div>
  <div class="btn">CONTACT US TODAY</div>
</section>

<section class="educational">
  <div class="edu-photo" role="img" aria-label="Group of smiling students with a girl in an orange top in front"></div>
  <div class="edu-panel">
    <h2 class="section-title">EDUCATONAL &amp; CULTURAL</h2>
    <ul class="edu-list">
      <li>Educational and cultural</li>
      <li>Professional teachers from Sydney universities</li>
      <li>A host family every day is easy to understand English</li>
      <li>Lessons from local schools, classrooms as well as cultural immersion activities</li>
      <li>How to live, get around, shop and socialise in Australia</li>
      <li>Activities in languages, food, religion and culture</li>
      <li>Outdoor activities and sport</li>
    </ul>
  </div>
</section>

<section class="safe">
  <h2 class="section-title">SAFE &amp; SECURE</h2>
  <div class="title-rule"></div>
  <div class="safe-cols">
    <ul>
      <li>Staff certified by the government for Working With Children</li>
      <li>Staff certified in first aid care</li>
      <li>Professional accommodation with excellent history in caring for children with extremely safe and practised Safety Management Procedures including</li>
      <li>Safety Management – reducing risk when taking students out of the classroom</li>
      <li>Safety &amp; Emergency Procedures (Location specific)</li>
    </ul>
    <ul>
      <li>Standard Operating Procedures</li>
      <li>Activity Specific Risk Management Plans</li>
      <li>Area Assessment Documentation</li>
      <li>Medical Form, Dietary Requirements Form, First Aid Incident &amp; Management Forms</li>
      <li>Clothing &amp; Equipment List</li>
    </ul>
  </div>
</section>

<section class="includes">
  <div class="includes-photo" role="img" aria-label="Sydney harbour bridge and skyline under a green tint"></div>
  <div class="includes-shade"></div>
  <h2 class="includes-title">INCLUDES</h2>
  <div class="inc-cols">
    <ul>
      <li><svg width="26" height="26" viewBox="0 0 26 26"><circle cx="13" cy="13" r="12" fill="#fff"/><path d="M8 13l3.5 3.5L18 10" stroke="#6f8f35" stroke-width="2.4" fill="none"/></svg>Return tickets</li>
      <li><svg width="26" height="26" viewBox="0 0 26 26"><circle cx="13" cy="13" r="12" fill="#fff"/><path d="M8 13l3.5 3.5L18 10" stroke="#6f8f35" stroke-width="2.4" fill="none"/></svg>Visa fees</li>
      <li><svg width="26" height="26" viewBox="0 0 26 26"><circle cx="13" cy="13" r="12" fill="#fff"/><path d="M8 13l3.5 3.5L18 10" stroke="#6f8f35" stroke-width="2.4" fill="none"/></svg>Travel &amp; medical insurance</li>
      <li><svg width="26" height="26" viewBox="0 0 26 26"><circle cx="13" cy="13" r="12" fill="#fff"/><path d="M8 13l3.5 3.5L18 10" stroke="#6f8f35" stroke-width="2.4" fill="none"/></svg>Accommodation</li>
      <li><svg width="26" height="26" viewBox="0 0 26 26"><circle cx="13" cy="13" r="12" fill="#fff"/><path d="M8 13l3.5 3.5L18 10" stroke="#6f8f35" stroke-width="2.4" fill="none"/></svg>Meals (breakfast, lunch and dinner)</li>
    </ul>
    <ul>
      <li><svg width="26" height="26" viewBox="0 0 26 26"><circle cx="13" cy="13" r="12" fill="#fff"/><path d="M8 13l3.5 3.5L18 10" stroke="#6f8f35" stroke-width="2.4" fill="none"/></svg>Transportation</li>
      <li><svg width="26" height="26" viewBox="0 0 26 26"><circle cx="13" cy="13" r="12" fill="#fff"/><path d="M8 13l3.5 3.5L18 10" stroke="#6f8f35" stroke-width="2.4" fill="none"/></svg>Courses and certificate</li>
      <li><svg width="26" height="26" viewBox="0 0 26 26"><circle cx="13" cy="13" r="12" fill="#fff"/><path d="M8 13l3.5 3.5L18 10" stroke="#6f8f35" stroke-width="2.4" fill="none"/></svg>Tourism</li>
      <li><svg width="26" height="26" viewBox="0 0 26 26"><circle cx="13" cy="13" r="12" fill="#fff"/><path d="M8 13l3.5 3.5L18 10" stroke="#6f8f35" stroke-width="2.4" fill="none"/></svg>Daily activities and excursions</li>
    </ul>
  </div>
</section>

<footer class="site-footer">
  <nav class="foot-nav"><span>Home</span><span>Tours</span><span>Contact</span><span>About Us</span></nav>
  <p class="copyright">© 2015 Bright Wattle Journeys. All rights reserved.</p>
  <div class="social"><span class="s1"></span><span class="s2"></span><span class="s3"></span></div>
</footer>

</body>
</html>
```